Book cover - Lanterns Along the Winding Quay

Book cover for Ebook (Quillet) and wrap around print cover (Bindwell) (back, front, and spine)

The book title (may slightly change by end of brief):
(MAIN TITLE) 'Lanterns Along the Winding Quay'
(SUB HEADING) 'A Practical Seasonal Garden Companion for Planting Bulbs, Pruning Hedges and Growing Fresh Herbs'
by Dr Owen Pratchard

I would like a bold, stand out cover. Contemporary. I would like to avoid stereotypical images of people looking anxious or worried. I would like the design to be more uplifting and hopeful, rather than focusing on the negative aspect of anxiety, but avoiding cliched photos of people raising their hands in the air, smiling and jumping etc. The cover should appeal to both men and women.

Trim size of book cover (for BindWell) is 5.25" x 8" back and front with a spine size of 0.477 inches
Updates

Reason: I have decided to extend the deadline by 1 more day, not because I am unhappy with the quality of the designs, but because a few designers have contacted me to explain they have had technical difficulties when submitting their files. Thanks everyone for the hard work and great designs.

Target Market(s)

Males and females (16+) who struggle with social anxiety and shyness

Industry/Entity Type

Social

Font styles to use
Serif

Requirements
Must have
• Bold cover that is modern and contemporary. For example, I like these covers:
• http://lnkvo.test/7kTq3Wm
• http://lnkvo.test/9gHw5Ze
• http://lnkvo.test/4nVy8Kb
• http://lnkvo.test/6jFu2Xo
• http://lnkvo.test/3mEs9Lt
• http://lnkvo.test/8hGz4Nd
• http://lnkvo.test/5bJk7Pv
Nice to have
• Open to abstract designs.
Should not have
• No stereotypical pictures of people who look anxious or worried. Avoid cliched photos of people raising their hands in the air, smiling and jumping etc.

```html
<!DOCTYPE html>
<html lang="en">
<head>
<meta charset="utf-8">
<title>Lanterns Along the Winding Quay — Book Cover</title>
<link rel="stylesheet" href="https://fonts.googleapis.com/css2?family=Kaushan+Script&family=Montserrat:wght@400;500;700&display=swap">
<style>
  :root {
    --backdrop: #c4c6b4;
    --paper: #ffffff;
    --sky-light: #e9f6fb;
    --aqua: #46c6e6;
    --ocean: #1f8fd0;
    --deep-ocean: #1560b4;
    --ink-blue: #1d4f9e;
    --title-blue: #2a8fd0;
    --script-blue: #1c5cb0;
    --white: #ffffff;
  }
  * { margin: 0; padding: 0; box-sizing: border-box; }
  html, body {
    width: 1200px;
    height: 1000px;
    overflow: hidden;
    background: var(--backdrop);
  }
  .canvas {
    position: relative;
    width: 1200px;
    height: 1000px;
  }
  .cover {
    position: absolute;
    left: 290px;
    top: 25px;
    width: 620px;
    height: 950px;
    overflow: hidden;
    background: linear-gradient(180deg,
      var(--paper) 0%,
      var(--paper) 22%,
      var(--sky-light) 36%,
      var(--aqua) 50%,
      var(--ocean) 68%,
      var(--deep-ocean) 100%);
    box-shadow: 0 6px 18px rgba(0,0,0,0.25);
  }
  .cover-swooshes {
    position: absolute;
    inset: 0;
    width: 620px;
    height: 950px;
  }
  .title-kicker,
  .title-joiner,
  .title-script,
  .subtitle,
  .author {
    position: absolute;
    left: 0;
    width: 100%;
    text-align: center;
  }
  .title-kicker {
    top: 68px;
    font-family: "Montserrat", sans-serif;
    font-weight: 700;
    font-size: 56px;
    letter-spacing: 2px;
    color: var(--title-blue);
  }
  .title-script {
    font-family: "Kaushan Script", cursive;
    line-height: 1;
  }
  .title-script--upper {
    top: 185px;
    font-size: 118px;
    color: var(--script-blue);
    text-shadow: 3px 4px 0 rgba(255,255,255,0.85);
    transform: rotate(-4deg);
  }
  .title-joiner {
    top: 440px;
    font-family: "Montserrat", sans-serif;
    font-weight: 700;
    font-size: 32px;
    letter-spacing: 1px;
    color: var(--ink-blue);
  }
  .title-script--lower {
    top: 498px;
    font-size: 128px;
    color: var(--white);
    text-shadow: 4px 5px 0 rgba(29,79,158,0.55);
    transform: rotate(-3deg);
  }
  .rule {
    position: absolute;
    left: 45px;
    width: 555px;
    height: 2px;
    background: var(--white);
  }
  .rule--top { top: 675px; }
  .rule--bottom { top: 778px; }
  .subtitle {
    top: 695px;
    padding: 0 40px;
    font-family: "Montserrat", sans-serif;
    font-weight: 500;
    font-size: 18px;
    line-height: 32px;
    color: var(--white);
  }
  .author {
    top: 832px;
    font-family: "Montserrat", sans-serif;
    font-weight: 400;
    font-size: 42px;
    letter-spacing: 1px;
    color: var(--white);
  }
</style>
</head>
<body>
  <main class="canvas">
    <section class="cover" aria-label="Front cover">
      <svg class="cover-swooshes" viewBox="0 0 620 950" aria-hidden="true">
        <path d="M0 185 C 120 170, 200 250, 330 240 S 520 190, 620 300"
              fill="none" stroke="var(--script-blue)" stroke-width="7" stroke-linecap="round"/>
        <path d="M0 575 C 90 540, 160 560, 260 552 S 480 520, 620 540"
              fill="none" stroke="var(--white)" stroke-width="8" stroke-linecap="round"/>
      </svg>

      <h1 class="book-title">
        <span class="title-kicker">LANTERNS</span>
        <span class="title-script title-script--upper">Along the</span>
        <span class="title-joiner">WINDING</span>
        <span class="title-script title-script--lower">Quay</span>
      </h1>

      <div class="rule rule--top"></div>
      <p class="subtitle">A Practical Seasonal Garden Companion for Planting Bulbs, Pruning Hedges and Growing Fresh Herbs</p>
      <div class="rule rule--bottom"></div>

      <p class="author">DR OWEN PRATCHARD</p>
    </section>
  </main>
</body>
</html>
```